July 2022 Industrial Manufacturer Product Expo Mexico City

We manufacture large screws and fastners for large Mining equipment, Trains, large ships, airplanes, wind turbines, and so on. We also do custom work base on the customer needs. No matter the size we can make it.
We have a Expo coming up with companies all over the world. We have to stand out we are a family own business so our customer service will be above and beyond anyone can provide. We do not have a sales force to push our products and services we provide one on one service.
Plus@!! I'm looking for anything that you designers can come up with if it was your company to put on a business card, plus i want to do a 1 or 2 sided pamphlet, and then a website. We make Speciality Bolts for large mining equipment these bolts can be 3 to 4 foot long!!! Plus fasteners, Nuts, washers, any, size, strengths, special materials, we offer more of a ono on one customer service, We are a small company, family own, but can fulfill any type of orders. We can also provide special time lines for emergency orders. "We keep the machines running we here at KRV don't believe in down time" We want to hear any slogan based on our company to stand out.
Thanks i really appreciate all your work and options that we have to pick on. Plus just a thought we could possibly want to entertain a experience Marketing internet help maybe a employment possibility. Thanks

I need 2 cards one in Spanish and English Like the steel back ground maybe send me in some bright red and blue writing Same with the Black cards Please remove the word Military The logo KRV maybe integrate a picture of a Bolt 🔩 Thank you

Still looking for I need 2 cards one in Spanish and English Like the steel back ground maybe send me in some bright red and blue writing Same with the Black cards try bright writing Please remove the word Military The logo KRV maybe integrate a picture of a Bolt 🔩 Plus will need the company to make a brochure and website next Thank you

Target Market(s)

Large Mining, Ship, Train, Green Energy, VELM, and Government equipment. Throughout the World

Industry/Entity Type

We can Custom Manufacture any type of Fastners for Mining equipment, Trains, Ships, Green energy, Governments, or military projects. wind turbines,

Contact Information for Business Card

I attached the name and contact info that's on a card, plus the Company Logo. Would like industrial looking background with Bright Colors that will stand out!! If we can insert somewhere maybe on back that we "Custom Manufacture Any Size or Quantity Fastners for Large Mining Equipment, Trains, Ships, Green Energy Equipment or Government Projects

Font styles to use
Other font styles liked:
• You Pick, has to be bold, colorful standout, Professional looking Beable to read it.

Colors

Designer to choose colors to be used in the design.

Requirements
Must have
• Need in Spanish and English TO STANDOUT FROM THE REST OF THE EXPO!! See Business card details, Rounded corners
Nice to have
• Can i see some of the darker cards with Bright Red and Blue letters I like to see the different type of card material, heavy thickness, plastic, transparent, Metal types, Bright Colors, I saw like Raised letters like on the logo.

```html
<!DOCTYPE html>
<html lang="es">
<head>
<meta charset="utf-8">
<title>KRV Business Card</title>
<link rel="stylesheet" href="https://fonts.googleapis.com/css2?family=Bebas+Neue&family=Tinos:wght@400;700&display=swap">
<style>
  :root {
    --backdrop: #b9b9b9;
    --card-white: #ffffff;
    --blue-top: #0298d8;
    --blue-mid: #0063b8;
    --blue-bottom: #001a7a;
    --sky: #1b95d4;
    --navy: #1a2470;
    --steel: #4a4a4d;
    --rule: #333333;
  }
  * { margin: 0; padding: 0; box-sizing: border-box; }
  html, body { width: 1200px; height: 1200px; overflow: hidden; }
  body { background: var(--backdrop); position: relative; }

  .card {
    position: absolute;
    top: 303px;
    width: 369px;
    height: 594px;
  }
  .card--back {
    left: 200px;
    background: linear-gradient(180deg, var(--blue-top) 0%, var(--blue-mid) 45%, var(--blue-bottom) 100%);
  }
  .card--front {
    left: 599px;
    width: 364px;
    background: var(--card-white);
  }

  .services { position: absolute; inset: 0; }
  .services text {
    font-family: 'Bebas Neue', sans-serif;
    fill: #ffffff;
    text-anchor: middle;
  }

  .brand-name {
    position: absolute;
    top: 455px;
    left: 0;
    width: 100%;
    top: 150px;
    text-align: center;
    font-family: 'Bebas Neue', sans-serif;
    font-size: 96px;
    letter-spacing: 12px;
    color: var(--steel);
    line-height: 1;
  }

  .contact {
    position: absolute;
    top: 402px;
    left: 0;
    width: 100%;
    text-align: center;
    font-family: 'Tinos', serif;
    color: var(--navy);
  }
  .contact__name { font-size: 19px; color: var(--sky); line-height: 24px; }
  .contact__rule { width: 61px; height: 1px; background: var(--rule); margin: 11px auto 8px; }
  .contact__line { font-size: 16px; line-height: 20px; }
  .contact__label { color: var(--sky); font-weight: 700; }
  .contact__phones { margin-top: 0; }
  .contact__phones .contact__line { line-height: 22px; letter-spacing: 0.5px; }
</style>
</head>
<body>
  <section class="card card--back" aria-label="Card back: services">
    <svg class="services" width="369" height="594" viewBox="0 0 369 594">
      <text x="184" y="127" font-size="32" textLength="252" lengthAdjust="spacingAndGlyphs">CUSTOM MANUFACTURE</text>
      <text x="184" y="176" font-size="34" textLength="257" lengthAdjust="spacingAndGlyphs">ANY SIZE OR QUANTITY</text>
      <text x="184" y="223" font-size="34" textLength="256" lengthAdjust="spacingAndGlyphs">FASTNERS FOR LARGE</text>
      <text x="184" y="271" font-size="35" textLength="254" lengthAdjust="spacingAndGlyphs">MINING EQUIPMENT</text>
      <text x="184" y="333" font-size="44" textLength="260" lengthAdjust="spacingAndGlyphs">TRAINS, SHIPS</text>
      <text x="184" y="372" font-size="30" textLength="257" lengthAdjust="spacingAndGlyphs">GREEN ENERGY EQUIPMENT</text>
      <text x="190" y="451" font-size="60" textLength="244" lengthAdjust="spacingAndGlyphs">MILITARY OR</text>
      <text x="188" y="509" font-size="31" textLength="243" lengthAdjust="spacingAndGlyphs">GOVERNMENT PROJECTS</text>
    </svg>
  </section>

  <section class="card card--front" aria-label="Card front: contact">
    <div class="brand-name">KRV</div>
    <div class="contact">
      <p class="contact__name">Lic. Mariana Solís Reyes</p>
      <div class="contact__rule"></div>
      <p class="contact__line">Cotizaciones en</p>
      <p class="contact__line">ventas@tornilleriakrv.mx</p>
      <div class="contact__rule"></div>
      <div class="contact__phones">
        <p class="contact__line"><span class="contact__label">P:</span> 8714406218</p>
        <p class="contact__line"><span class="contact__label">M:</span> 8713359027</p>
      </div>
    </div>
  </section>
</body>
</html>
```